Moon Tot needs ecommerce website design help

We need someone to set up a fully functional website for us. We sell baby bibs, I attached them along with our company logo (MTG: moon tot goods). The bibs are made of 100% silicon, they are safe, light weight, soft, smooth, flexible, dishwasher safe and has funny faces.

Business name: Moon Tot Goods
Elm Hollow, NY 00000
email: MoonTotGoods@mailbox-example.com
tel.: (555) 014-TOTS
website: MoonTotGoods-example.com

Target Market(s)

18-40

Industry/Entity Type

Baby

Coding

Coded - Design and coding required

Number of Pages Required

5+ page

Requirements
Must have
• 1. Pages: Why buy from us, Contact Us, Home page, Products Page, Blog
• 2. Use the colors from our logo for the web design.
• 3. Need a link that will connect visitors to our facebook, instagram, Pinterest and Tumblr account. Would like links on,the top left side of the page
Nice to have
• My Cart page
• 1. On contact us page, we want to include some type of template for the customer to complete. (Ex: name, email address, contact number, optional home address, comments)
• 2. When clients visit our website, we want a capture/pop up for the customer to subscribe to our email list to receive discounts. (Ex. Want 10% off your next order ? Suscribe to our mailing list below and get a 10% off code to use at check out. If they don't want to subscribe, they have the option to select "No Thank You, I want to pay full price).
• 3. On home page have subscribe to our email list.

```html
<!DOCTYPE html>
<html lang="en">
<head>
<meta charset="utf-8">
<title>Moon Tot Goods</title>
<link href="https://fonts.googleapis.com/css2?family=Raleway:wght@400;500;600;700&family=Open+Sans:wght@400;600&display=swap" rel="stylesheet">
<style>
:root{
  --pink:#e61f6f;
  --pink-dark:#c9155a;
  --green:#6bb526;
  --green-dark:#4f8f16;
  --orange:#f47a20;
  --blue:#1f9be0;
  --yellow:#f0dd1c;
  --sky:#eaf4fb;
  --text:#444;
  --muted:#666;
  --line:#e6e6e6;
}
*{box-sizing:border-box;margin:0;padding:0}
html,body{width:870px;height:1200px;overflow:hidden}
body{position:relative;background:linear-gradient(#e4f0fa,#f2f7fb 40%,#f4f8fb);font-family:"Open Sans",sans-serif;color:var(--text)}
.abs{position:absolute}

.brand{left:76px;top:20px;display:flex;align-items:center;gap:8px}
.brand-dot{width:54px;height:54px;border-radius:50%;background:var(--green)}
.brand-name{font-family:"Raleway",sans-serif;font-weight:700;font-size:16px;color:var(--pink);letter-spacing:.2px}

.social-top{right:66px;top:19px;display:flex;gap:6px}
.social-top span{width:26px;height:26px;border-radius:50%;display:block}

.nav{left:346px;top:58px;display:flex;gap:4px}
.nav a{display:block;color:#fff;text-decoration:none;font-family:"Raleway",sans-serif;font-weight:600;font-size:10.5px;text-transform:uppercase;padding:12px 18px 10px;border-radius:3px 3px 0 0;box-shadow:0 2px 3px rgba(0,0,0,.15)}
.nav .home{background:var(--green);transform:rotate(-5deg) translateY(4px)}
.nav .products{background:var(--pink);transform:rotate(3deg)}
.nav .why{background:var(--orange);transform:rotate(5deg) translateY(2px)}
.nav .blog{background:var(--blue);transform:rotate(-6deg) translateY(2px)}
.nav .contact{background:var(--yellow);transform:rotate(-10deg) translateY(-2px)}

.hero{left:70px;top:96px;width:728px;height:380px;background:#fff;padding:6px;box-shadow:0 1px 3px rgba(0,0,0,.12)}
.hero-photo{position:relative;width:100%;height:100%;background:linear-gradient(100deg,#b9c93a 0%,#d6d36a 35%,#e9e2b6 55%,#c7c35a 80%,#9aa552 100%)}
.hero-copy{position:absolute;left:486px;top:190px;color:#fff}
.hero-copy h1{font-family:"Raleway",sans-serif;font-weight:700;font-size:32px;line-height:1}
.hero-copy p{font-family:"Raleway",sans-serif;font-size:16px;line-height:20px;margin-top:6px;text-transform:uppercase}
.btn{display:inline-block;background:linear-gradient(var(--green),var(--green-dark));color:#fff;font-family:"Raleway",sans-serif;font-weight:600;text-transform:uppercase;border-radius:2px}
.hero-copy .btn{margin-top:8px;font-size:10px;padding:8px 16px}
.dots{position:absolute;left:306px;top:330px;display:flex;gap:3px}
.dots span{width:12px;height:12px;border-radius:50%;border:2px solid #fff}
.dots .on{background:var(--pink);border-color:var(--pink)}

.newsletter{left:70px;top:480px;width:728px;height:66px;background:linear-gradient(var(--pink),var(--pink-dark));display:flex;align-items:center;padding:0 14px 0 26px}
.newsletter-icon{width:52px;height:52px;border:1.5px dashed #fff;border-radius:50%;display:flex;align-items:center;justify-content:center}
.newsletter h2{font-family:"Raleway",sans-serif;font-weight:500;font-size:16px;color:#fff;margin:0 16px 0 12px;white-space:nowrap}
.field{width:170px;height:26px;background:#fff;font-size:8.5px;color:#888;padding:7px 9px;margin-right:5px}
.newsletter .btn{margin-left:5px;font-size:10.5px;padding:7px 18px;font-weight:700}

.category{left:70px;top:567px;width:216px;background:#fff;box-shadow:0 1px 3px rgba(0,0,0,.1)}
.category-head{background:linear-gradient(var(--pink),var(--pink-dark));color:#fff;font-family:"Raleway",sans-serif;font-weight:700;font-size:13px;padding:10px 14px;display:flex;justify-content:space-between;align-items:center}
.category ul{list-style:none;padding:4px 0 2px}
.category li{display:flex;align-items:center;font-size:8px;color:var(--muted);text-transform:uppercase;height:25.5px;border-bottom:1px solid var(--line);padding:0 16px 0 20px}
.category li:last-child{border-bottom:none}
.category li .chev{width:20px;color:#999}
.category li .txt{flex:1}
.category li .go{width:7px;height:7px;border-radius:50%;background:#555}

.promo{left:70px;top:862px;width:216px;height:129px;background:#fff;padding:4px;box-shadow:0 1px 3px rgba(0,0,0,.12)}
.promo-photo{position:relative;width:100%;height:100%;background:linear-gradient(120deg,#b98a5c,#7c5232 55%,#4a7fae)}
.promo-copy{position:absolute;left:6px;top:62px;color:#fff;font-family:"Raleway",sans-serif;font-weight:500}
.promo-copy .l1{font-size:19px}
.promo-copy .l2{font-size:29px;font-weight:700;margin-left:28px;line-height:1}
.promo-copy .l2 small{font-size:16px}

.card{width:154px;height:202px;background:#fff;box-shadow:0 1px 3px rgba(0,0,0,.12);padding:3px}
.card-photo{position:relative;height:104px}
.sale{position:absolute;left:14px;top:4px;width:30px;height:30px;border-radius:50%;background:var(--green);color:#fff;font-size:6.5px;font-weight:600;display:flex;align-items:center;justify-content:center}
.card h3{font-family:"Raleway",sans-serif;font-weight:600;font-size:9.5px;color:#444;margin:19px 0 0 14px}
.price{margin:6px 0 0 14px;font-size:10px;color:#333;display:flex;align-items:center;gap:6px}
.stars{color:#f5a11a;font-size:8px;letter-spacing:.5px}
.card .btn{margin:12px 0 0 14px;font-size:8px;font-weight:500;padding:7px 14px}

.footer-wave{left:0;top:1036px;width:870px;height:30px}
.footer{left:0;top:1064px;width:870px;height:100px;background:var(--pink);color:#fff}
.contact-item{position:absolute;top:18px;display:flex;gap:10px;font-size:8.5px;line-height:14px}
.contact-icon{width:26px;height:26px;border:1.5px solid #fff;border-radius:50%;display:flex;align-items:center;justify-content:center;flex:none}
.contact-item .big{font-size:14px;font-family:"Raleway",sans-serif}
.social-foot{position:absolute;left:682px;top:28px;display:flex;gap:6px}
.social-foot span{width:25px;height:25px;border:1.5px solid #fff;border-radius:50%;display:block}
.copyright{left:0;top:1164px;width:870px;height:36px;background:var(--pink-dark);color:#fff;font-size:8.5px;display:flex;align-items:center;justify-content:center}
</style>
</head>
<body>

<header>
  <div class="abs brand"><span class="brand-dot"></span><span class="brand-name">MOON TOT GOODS</span></div>
  <div class="abs social-top" aria-label="Social links">
    <span style="background:var(--green)"></span>
    <span style="background:var(--pink)"></span>
    <span style="background:var(--orange)"></span>
    <span style="background:var(--blue)"></span>
  </div>
  <nav class="abs nav">
    <a class="home">Home</a>
    <a class="products">Products</a>
    <a class="why">Why buy from us</a>
    <a class="blog">Blog</a>
    <a class="contact">Contact us</a>
  </nav>
</header>

<section class="abs hero">
  <div class="hero-photo" role="img" aria-label="Toddler in a high chair eating with a spoon, wearing a pink silicone bib">
    <div class="hero-copy">
      <h1>BABY BIBS</h1>
      <p>Made of 100% silicon<br>They are safe</p>
      <span class="btn">Shop now</span>
    </div>
    <div class="dots"><span class="on"></span><span></span><span></span><span></span></div>
  </div>
</section>

<section class="abs newsletter">
  <div class="newsletter-icon">
    <svg width="26" height="18" viewBox="0 0 26 18" fill="none" stroke="#fff" stroke-width="1.5"><rect x="1" y="1" width="24" height="16"/><path d="M1 1l12 9 12-9"/></svg>
  </div>
  <h2>NEWSLETTER SIGN UP</h2>
  <div class="field">Enter your name...</div>
  <div class="field">Enter your password...</div>
  <span class="btn">Subscribe</span>
</section>

<aside class="abs category">
  <div class="category-head">PRODUCTS CATEGORY
    <svg width="12" height="10" viewBox="0 0 12 10" fill="#fff"><rect width="12" height="2"/><rect y="4" width="12" height="2"/><rect y="8" width="12" height="2"/></svg>
  </div>
  <ul>
    <li><span class="chev">›</span><span class="txt">Silicon products</span><span class="go"></span></li>
    <li><span class="chev">›</span><span class="txt">They are safe</span><span class="go"></span></li>
    <li><span class="chev">›</span><span class="txt">Light weight</span><span class="go"></span></li>
    <li><span class="chev">›</span><span class="txt">Soft products</span><span class="go"></span></li>
    <li><span class="chev">›</span><span class="txt">Smooth products</span><span class="go"></span></li>
    <li><span class="chev">›</span><span class="txt">Flexible products</span><span class="go"></span></li>
    <li><span class="chev">›</span><span class="txt">Dishwasher safe</span><span class="go"></span></li>
    <li><span class="chev">›</span><span class="txt">Silicon light products</span><span class="go"></span></li>
    <li><span class="chev">›</span><span class="txt">They are safe wight</span><span class="go"></span></li>
  </ul>
</aside>

<div class="abs promo">
  <div class="promo-photo" role="img" aria-label="Smiling infant wearing a blue bib">
    <div class="promo-copy"><div class="l1">UPTO SAVE</div><div class="l2">30<small>%</small></div></div>
  </div>
</div>

<main>
  <article class="abs card" style="left:306px;top:566px">
    <div class="card-photo" role="img" aria-label="Pink silicone bib with a funny face" style="background:radial-gradient(circle at 50% 55%,#e8318a 0 28%,#f2f2f2 45%)"><span class="sale">SALE</span></div>
    <h3>NEQUE PORRO QUISQUAM</h3><div class="price">$ 44.00 <span class="stars">★★★★★</span></div><span class="btn">Shop now</span>
  </article>
  <article class="abs card" style="left:474px;top:566px">
    <div class="card-photo" role="img" aria-label="Blue silicone bib with a funny face" style="background:radial-gradient(circle at 50% 55%,#2a8fe0 0 28%,#f2f2f2 45%)"></div>
    <h3>NEQUE PORRO QUISQUAM</h3><div class="price">$ 44.00 <span class="stars">★★★★★</span></div><span class="btn">Shop now</span>
  </article>
  <article class="abs card" style="left:642px;top:566px">
    <div class="card-photo" role="img" aria-label="Green frog-face silicone bib" style="background:radial-gradient(circle at 50% 55%,#6cc02a 0 28%,#f2f2f2 45%)"></div>
    <h3>NEQUE PORRO QUISQUAM</h3><div class="price">$ 44.00 <span class="stars">★★★★★</span></div><span class="btn">Shop now</span>
  </article>
  <article class="abs card" style="left:306px;top:790px">
    <div class="card-photo" role="img" aria-label="Orange tiger-face silicone bib" style="background:radial-gradient(circle at 50% 55%,#f58c16 0 28%,#f2f2f2 45%)"></div>
    <h3>NEQUE PORRO QUISQUAM</h3><div class="price">$ 44.00 <span class="stars">★★★★★</span></div><span class="btn">Shop now</span>
  </article>
  <article class="abs card" style="left:474px;top:790px">
    <div class="card-photo" role="img" aria-label="Blue shark-face silicone bib" style="background:radial-gradient(circle at 50% 55%,#1c7fe0 0 28%,#f2f2f2 45%)"></div>
    <h3>NEQUE PORRO QUISQUAM</h3><div class="price">$ 44.00 <span class="stars">★★★★★</span></div><span class="btn">Shop now</span>
  </article>
  <article class="abs card" style="left:642px;top:790px">
    <div class="card-photo" role="img" aria-label="Yellow silicone bib with a funny face" style="background:radial-gradient(circle at 50% 55%,#eee21a 0 28%,#f2f2f2 45%)"></div>
    <h3>NEQUE PORRO QUISQUAM</h3><div class="price">$ 44.00 <span class="stars">★★★★★</span></div><span class="btn">Shop now</span>
  </article>
</main>

<svg class="abs footer-wave" viewBox="0 0 870 30" preserveAspectRatio="none">
  <path fill="var(--pink)" d="M0 30 V14 Q20 2 40 8 Q70 -4 110 12 Q150 -2 190 14 Q230 0 270 10 Q300 -4 340 12 Q380 0 420 14 Q460 2 500 10 Q540 -4 580 12 Q620 0 660 14 Q700 2 740 10 Q780 -4 820 12 Q850 2 870 8 V30 Z"/>
</svg>

<footer class="abs footer">
  <div class="contact-item" style="left:72px">
    <span class="contact-icon"><svg width="13" height="10" viewBox="0 0 13 10" fill="none" stroke="#fff" stroke-width="1.2"><rect x=".6" y=".6" width="11.8" height="8.8"/><path d="M.6.6l5.9 4.6L12.4.6"/></svg></span>
    <div>Email:<br>MoonTotGoods@mailbox-example.com</div>
  </div>
  <div class="contact-item" style="left:286px">
    <span class="contact-icon"><svg width="10" height="14" viewBox="0 0 10 14" fill="none" stroke="#fff" stroke-width="1.3"><path d="M5 13C2 9 1 7 1 5a4 4 0 0 1 8 0c0 2-1 4-4 8z"/><circle cx="5" cy="5" r="1.4"/></svg></span>
    <div>Address:<br>Moon Tot Goods<br>Elm Hollow, NY 00000</div>
  </div>
  <div class="contact-item" style="left:472px">
    <span class="contact-icon"><svg width="12" height="12" viewBox="0 0 12 12" fill="none" stroke="#fff" stroke-width="1.3"><path d="M2 1l2.5 0 1 3-1.5 1a7 7 0 0 0 3 3l1-1.5 3 1V10c0 .6-.4 1-1 1C5 11 1 7 1 2c0-.6.4-1 1-1z"/></svg></span>
    <div>Call to us<br><span class="big">(555) 014-TOTS</span></div>
  </div>
  <div class="social-foot"><span></span><span></span><span></span><span></span></div>
</footer>

<div class="abs copyright">© Copyrights moontotgoods 2016.All Rights Resevered.</div>

</body>
</html>
```